Engagement party email invitation

I need an invitation designed for my upcoming engagement party. I would like the attached picture to be encircled by gum leaves or some sort of garland of green leaves.

Traditional text typeface eg Sackers Gothic Light or Mrs Eaves.

Thanks
Marnie

Font styles to use
Serif
Script

```html
<!DOCTYPE html>
<html lang="en">
<head>
<meta charset="utf-8">
<title>Engagement Party Invitation</title>
<link rel="stylesheet" href="https://fonts.googleapis.com/css2?family=Questrial&display=swap">
<style>
  :root {
    --backdrop: #ffffff;
    --card: #f6f6f6;
    --card-glow: #ffffff;
    --ink: #2b2b2b;
    --accent: #6aab1e;
    --leaf-light: #9fdc4a;
    --leaf-mid: #5fbf26;
    --leaf-deep: #3f9a1a;
  }
  html, body {
    margin: 0;
    padding: 0;
    width: 1200px;
    height: 800px;
    overflow: hidden;
    background: var(--backdrop);
  }
  .canvas {
    position: relative;
    width: 1200px;
    height: 800px;
  }
  .invitation {
    position: absolute;
    left: 220px;
    top: 20px;
    width: 760px;
    height: 760px;
    background: radial-gradient(circle at 50% 52%, var(--card-glow) 0%, var(--card) 70%);
  }
  .leaf-garland {
    position: absolute;
    left: 0;
    top: 0;
    width: 760px;
    height: 760px;
  }
  .invitation-text {
    position: absolute;
    left: 227px;
    top: 290px;
    width: 360px;
    margin: 0;
    text-align: center;
    font-family: "Questrial", sans-serif;
    font-variant: small-caps;
    color: var(--ink);
  }
  .invitation-text p {
    margin: 0;
    font-size: 19px;
    letter-spacing: 0.14em;
    line-height: 37px;
  }
  .invitation-text .couple {
    font-size: 29px;
    color: var(--accent);
    letter-spacing: 0.1em;
    line-height: 44px;
    margin: 0 0 12px;
  }
</style>
</head>
<body>
<main class="canvas">
  <section class="invitation">
    <svg class="leaf-garland" viewBox="0 0 760 760" role="img" aria-label="Circular garland of fresh green leaves framing the invitation text">
      <defs>
        <linearGradient id="garland-tone" x1="0" y1="0" x2="1" y2="1">
          <stop offset="0" stop-color="var(--leaf-mid)"/>
          <stop offset="0.5" stop-color="var(--leaf-light)"/>
          <stop offset="1" stop-color="var(--leaf-deep)"/>
        </linearGradient>
      </defs>
      <circle cx="380" cy="400" r="290" fill="none" stroke="url(#garland-tone)" stroke-width="44" opacity="0.55"/>
      <path d="M 230 150 A 290 290 0 0 0 340 688" fill="none" stroke="url(#garland-tone)" stroke-width="46" opacity="0.5"/>
    </svg>
    <div class="invitation-text">
      <p>You are cordially invited to an</p>
      <p>Engagement Party honoring</p>
      <p class="couple">Eliza and Marnie!</p>
      <p>Come toast the couple with us</p>
      <p>on Sunday, July 18th at 2pm</p>
    </div>
  </section>
</main>
</body>
</html>
```